Personal Web page for recruiter and owner of consulting firm

I work full time as a recruiter so I want a page that allows for me to support my efforts. I would like a long single page, I need to be able to upload four two minute videos, and 4 images. I also want the color scheme to match with my consulting company. I own the domain marcusfenwold.net already through wordpress . I took a shot at it myself and its terrible.

Target Market(s)

Potential clients

Industry/Entity Type

Management Consulting

Logo Text

marcus fenwold

Font styles to use
Serif

Requirements
Must have
• Must in color scheme go well with my consulting company logo attached
• Must be able to upload 4 two minute videos and 4 images (photos of me)
• Single long scroll page
• Modern and clean
Nice to have
• Easy for me to update videos images and text without complex coding
Should not have
• I want the design and feel to go well with my logos not exactly replicate it

```html
<!DOCTYPE html>
<html lang="en">
<head>
<meta charset="utf-8">
<title>Halvern Strategies – Recruiter &amp; Consulting</title>
<link href="https://fonts.googleapis.com/css2?family=Open+Sans:wght@400;600;700&family=Raleway:wght@400;500;600;700&family=Roboto+Condensed:wght@700&display=swap" rel="stylesheet">
<style>
:root{
  --navy:#0f2d5c;
  --navy-deep:#0b2550;
  --heading:#1b2f55;
  --accent:#1c5aa6;
  --text:#555b66;
  --muted:#8a8f98;
  --line:#d9dde3;
  --white:#ffffff;
  --paper:#f4f2ee;
}
*{margin:0;padding:0;box-sizing:border-box}
html,body{width:1200px;height:4245px;overflow:hidden}
body{font-family:"Open Sans",Arial,sans-serif;color:var(--text);background:var(--white);position:relative}
section,header,footer{position:absolute;left:0;width:1200px}
.abs{position:absolute}
.photo{position:absolute;display:block}
.play{position:absolute;width:64px;height:64px;border:3px solid rgba(255,255,255,.85);border-radius:50%;}
.play::after{content:"";position:absolute;left:23px;top:17px;border-left:20px solid rgba(255,255,255,.9);border-top:12px solid transparent;border-bottom:12px solid transparent}
.section-title{position:absolute;left:0;width:1200px;text-align:center;font-family:"Raleway",sans-serif;font-weight:600;font-size:31px;color:var(--heading);letter-spacing:.5px}
.title-rule{position:absolute;left:575px;width:50px;height:3px;background:var(--navy)}

/* Hero */
.hero{top:0;height:637px;background:linear-gradient(120deg,#2c4f80 0%,#5d7fa8 40%,#1f3a66 75%,#0f2547 100%)}
.brand{position:absolute;left:98px;top:40px;font-family:"Raleway",sans-serif;font-weight:500;color:var(--white);font-size:30px;letter-spacing:3px;line-height:1.15}
.brand small{display:block;font-size:15px;letter-spacing:5px;padding-left:46px}
.menu-btn{position:absolute;left:1020px;top:44px;width:80px;height:30px;border:1px solid rgba(255,255,255,.8);border-radius:3px;color:var(--white);font-size:13px;font-weight:700;display:flex;align-items:center;justify-content:center;gap:6px}
.menu-btn i{display:block;width:12px;height:2px;background:#fff;box-shadow:0 4px 0 #fff,0 -4px 0 #fff}
.hero-title{position:absolute;top:308px;width:1200px;text-align:center;font-family:"Roboto Condensed",sans-serif;font-weight:700;font-size:56px;color:var(--white);letter-spacing:.5px}
.hero-sub{position:absolute;top:380px;width:1200px;text-align:center;font-size:22px;font-weight:600;color:var(--white)}
.dots{position:absolute;top:424px;left:572px;display:flex;gap:8px}
.dots span{width:12px;height:12px;border-radius:50%;border:2px solid #fff}
.dots span.on{background:#fff}

/* What we do */
.what{top:637px;height:481px}
.what .section-title{top:60px}
.feature{position:absolute;top:170px;width:240px;text-align:center}
.feature svg{width:72px;height:72px}
.feature h3{font-family:"Raleway",sans-serif;font-weight:500;font-size:18px;color:var(--heading);margin:18px 0 12px}
.feature p{font-size:12px;line-height:1.55;color:var(--muted)}
.read{font-size:11px;color:var(--text);margin-top:16px;letter-spacing:.3px}
.read::after{content:" ▸"}

/* About */
.about{top:1118px;height:504px;background:linear-gradient(100deg,#203f6e 0%,#284c7f 50%,#1a3862 100%)}
.about h2{position:absolute;left:98px;top:112px;font-family:"Raleway",sans-serif;font-weight:700;font-size:31px;color:var(--white)}
.about .copy{position:absolute;left:98px;top:160px;width:500px;color:#e3e9f2;font-size:12px;line-height:1.6}
.about .copy p{margin-bottom:12px}
.about ul{list-style:none;margin-top:18px}
.about li{margin-bottom:8px;padding-left:18px;position:relative}
.about li::before{content:"";position:absolute;left:0;top:5px;width:8px;height:8px;border-radius:50%;background:#e3e9f2}
.about-video{left:637px;top:107px;width:467px;height:284px;border:4px solid #dfe6ef;background:linear-gradient(135deg,#7e93ad,#c6ccd3 50%,#4d6583)}

/* Services */
.services{top:1622px;height:614px}
.services .section-title{top:82px}
.services .title-rule{top:138px}
.service{position:absolute;top:192px;width:311px}
.service .photo{position:relative;width:311px;height:181px}
.service h3{font-family:"Raleway",sans-serif;font-weight:500;font-size:16px;color:#333;margin:22px 0 10px}
.service p{font-size:11px;line-height:1.55;color:var(--muted)}
.btn-outline{display:inline-block;margin-top:14px;border:1px solid #aab;padding:4px 8px;font-size:10px;color:#333}
.btn-outline::after{content:" ●";color:#888}

/* Jobs */
.jobs{top:2236px;height:566px;background:linear-gradient(90deg,#fff 50%,#eeeeee)}
.jobs-photo{left:0;top:0;width:580px;height:566px;background:linear-gradient(120deg,#e8e6e2,#c9cdd3 40%,#2c3d5e 70%,#d7d4cf)}
.jobs-panel{left:430px;top:107px;width:770px;height:352px;background:var(--white);padding:42px 50px}
.jobs-panel h2{font-family:"Raleway",sans-serif;font-weight:500;font-size:31px;color:var(--accent)}
.wave{display:block;margin-top:6px}
.role{position:absolute;top:150px;width:200px}
.role .ico{width:60px;height:60px;border:2px solid var(--navy);border-radius:4px;display:flex;align-items:center;justify-content:center}
.role h3{font-family:"Raleway",sans-serif;font-weight:500;font-size:17px;color:#333;margin:14px 0 8px}
.role p{font-size:11px;line-height:1.55;color:var(--muted)}

/* News */
.news{top:2802px;height:674px}
.news .section-title{top:88px}
.post{position:absolute;top:167px;width:458px}
.post .photo{position:relative;width:458px;height:260px}
.post h3{font-family:"Raleway",sans-serif;font-weight:500;font-size:17px;color:#333;margin:20px 0 10px}
.post .meta{font-size:12px;color:#444;display:flex;align-items:center;gap:8px}
.post p{font-size:11px;line-height:1.6;color:var(--muted);margin-top:10px;padding-bottom:16px;border-bottom:1px solid var(--line)}

/* Contact */
.contact{top:3476px;height:416px;background:linear-gradient(180deg,#f1efea,#e8e4dc)}
.contact .section-title{top:70px}
.field{position:absolute;background:var(--white);border:1px solid #e0ddd6;font-size:11px;color:#666;padding:10px 12px}
.submit{position:absolute;left:529px;top:322px;width:142px;height:34px;background:var(--navy);color:var(--white);font-size:13px;font-weight:700;letter-spacing:1px;display:flex;align-items:center;justify-content:center}

/* Footer */
.footer{top:3892px;height:353px;background:var(--navy-deep);color:#dbe3ef}
.footer .brand{left:98px;top:50px;font-size:28px}
.footer h4{position:absolute;top:58px;font-family:"Raleway",sans-serif;font-weight:600;font-size:16px;color:var(--white);letter-spacing:.5px}
.contact-list{position:absolute;left:98px;top:150px;font-size:12px;line-height:1.5;list-style:none}
.contact-list li{display:flex;gap:14px;margin-bottom:20px}
.links{position:absolute;left:414px;top:100px;list-style:none;font-size:12px;line-height:1.95}
.links li::before{content:"▸ ";font-size:10px}
.newsletter{position:absolute;left:645px;top:100px;width:290px;font-size:11px;line-height:1.5}
.newsletter .input{margin-top:14px;height:40px;background:var(--white);color:#666;padding:11px 10px}
.newsletter .subscribe{display:inline-block;margin-top:12px;background:#1d1d1d;color:#fff;font-size:11px;padding:8px 12px;letter-spacing:.5px}
.social{position:absolute;left:1000px;top:100px;list-style:none;font-size:13px}
.social li{display:flex;align-items:center;gap:8px;margin-bottom:14px}
.social li span{width:26px;height:26px;border:1px solid #dbe3ef;border-radius:50%}
.copyright{position:absolute;left:0;top:298px;width:1200px;border-top:1px solid rgba(255,255,255,.15);padding-top:18px;text-align:center;font-size:11px;color:#b8c4d6}
</style>
</head>
<body>

<header class="hero">
  <div class="photo" role="img" aria-label="Business team reviewing documents at a desk" style="inset:0;background:linear-gradient(120deg,rgba(20,40,80,.2),rgba(10,25,55,.45))"></div>
  <div class="brand">HALVERN<small>STRATEGIES</small></div>
  <div class="menu-btn"><i></i>MENU</div>
  <div class="play" style="left:568px;top:228px"></div>
  <h1 class="hero-title">RECRUITER &amp; CONSULTING</h1>
  <p class="hero-sub">Sed ut perspiciatis unde omnis iste natus</p>
  <div class="dots"><span class="on"></span><span></span><span></span></div>
</header>

<section class="what">
  <h2 class="section-title">WHAT WE DO</h2>
  <div class="feature" style="left:100px">
    <svg viewBox="0 0 72 72"><path d="M22 60V46c-6-5-9-11-8-19 1-11 10-19 22-19s21 9 21 21c0 4 2 7 5 11l-5 2v8h-9v10z" fill="var(--navy)"/><circle cx="36" cy="28" r="8" fill="none" stroke="#fff" stroke-width="3"/><circle cx="36" cy="28" r="3" fill="#fff"/></svg>
    <h3>IT Recruiting</h3>
    <p>Sed ut perspiciatis unde omnis iste<br>natus error sit voluptatem accusantium<br>doloremque laudantium.</p>
    <div class="read">READ MORE</div>
  </div>
  <div class="feature" style="left:360px">
    <svg viewBox="0 0 72 72"><rect x="30" y="10" width="34" height="24" fill="none" stroke="var(--navy)" stroke-width="3"/><circle cx="20" cy="18" r="6" fill="var(--navy)"/><path d="M12 28h16l8-4 2 3-10 7v30h-6V48h-4v16h-6z" fill="var(--navy)"/><path d="M40 42v22M56 42v22M36 42h24" stroke="var(--navy)" stroke-width="3"/></svg>
    <h3>IT Training</h3>
    <p>Sed ut perspiciatis unde omnis iste<br>natus error sit voluptatem accusantium<br>doloremque laudantium.</p>
    <div class="read">READ MORE</div>
  </div>
  <div class="feature" style="left:617px">
    <svg viewBox="0 0 72 72"><path d="M16 52a12 12 0 0 1 2-24 18 18 0 0 1 35-4 14 14 0 0 1 3 28z" fill="var(--navy)"/><rect x="28" y="36" width="16" height="12" rx="2" fill="#fff"/><path d="M31 36v-4a5 5 0 0 1 10 0v4" fill="none" stroke="#fff" stroke-width="2.5"/></svg>
    <h3>Consulting</h3>
    <p>Sed ut perspiciatis unde omnis iste<br>natus error sit voluptatem accusantium<br>doloremque laudantium.</p>
    <div class="read">READ MORE</div>
  </div>
  <div class="feature" style="left:876px">
    <svg viewBox="0 0 72 72"><circle cx="36" cy="38" r="24" fill="none" stroke="var(--navy)" stroke-width="4"/><rect x="32" y="6" width="8" height="8" fill="var(--navy)"/><path d="M26 28l20 20" stroke="var(--navy)" stroke-width="4"/><circle cx="36" cy="38" r="3" fill="var(--navy)"/></svg>
    <h3>Strategy</h3>
    <p>Sed ut perspiciatis unde omnis iste<br>natus error sit voluptatem accusantium<br>doloremque laudantium.</p>
    <div class="read">READ MORE</div>
  </div>
</section>

<section class="about">
  <h2>ABOUT HALVERN STRATEGIES</h2>
  <div class="copy">
    <p>Sed ut perspiciatis unde omnis iste natus error sit voluptatem accusantium doloremque laudantium, totam rem aperiam, eaque ipsa quae ab illo inventore veritatis et quasi architecto beatae vitae dicta sunt explicabo. Nemo enim ipsam.</p>
    <p>Sed ut perspiciatis unde omnis iste natus error sit voluptatem accusantium doloremque laudantium, totam rem aperiam, eaque ipsa quae.</p>
    <ul>
      <li>Neque porro quisquam est, qui dolorem ipsum quia dolor</li>
      <li>Ut enim ad minima veniam, quis nostrum</li>
      <li>Sed ut perspiciatis unde omnis iste natus</li>
      <li>Excepteur sint occaecat cupidatat non</li>
    </ul>
  </div>
  <div class="photo about-video" role="img" aria-label="Video still of a team meeting around a laptop"></div>
  <div class="play" style="left:838px;top:217px"></div>
</section>

<section class="services">
  <h2 class="section-title">OUR SERVICES</h2>
  <div class="title-rule"></div>
  <div class="service" style="left:100px">
    <div class="photo" role="img" aria-label="Consultant working with a digital interface" style="background:linear-gradient(135deg,#14244a,#3a5f9a 55%,#0d1a36)"></div>
    <h3>Sed ut perspiciatis unde omnis iste</h3>
    <p>Sed ut perspiciatis unde omnis iste natus error sit voluptatem accusantium doloremque laudantium, totam</p>
    <span class="btn-outline">READ MORE</span>
  </div>
  <div class="service" style="left:444px">
    <div class="photo" role="img" aria-label="Colleagues discussing work over a laptop" style="background:linear-gradient(135deg,#cfc8bf,#8c7d70 50%,#4b4a55)"></div>
    <h3>Sed ut perspiciatis unde omnis iste</h3>
    <p>Sed ut perspiciatis unde omnis iste natus error sit voluptatem accusantium doloremque laudantium, totam</p>
    <span class="btn-outline">READ MORE</span>
  </div>
  <div class="service" style="left:789px">
    <div class="photo" role="img" aria-label="Hands reviewing charts on a desk" style="background:linear-gradient(135deg,#e8e2dc,#b89d8e 50%,#e6e3e0)"></div>
    <h3>Sed ut perspiciatis unde omnis iste</h3>
    <p>Sed ut perspiciatis unde omnis iste natus error sit voluptatem accusantium doloremque laudantium, totam</p>
    <span class="btn-outline">READ MORE</span>
  </div>
</section>

<section class="jobs">
  <div class="photo jobs-photo" role="img" aria-label="Businessman in a suit seated at a conference table"></div>
  <div class="abs jobs-panel">
    <h2>We Find You Jobs At Great Companies.</h2>
    <svg class="wave" width="52" height="8" viewBox="0 0 52 8"><path d="M0 4q6.5-6 13 0t13 0 13 0 13 0" fill="none" stroke="var(--accent)" stroke-width="2"/></svg>
    <div class="role" style="left:50px">
      <div class="ico"><svg width="32" height="26" viewBox="0 0 32 26"><circle cx="16" cy="7" r="5" fill="var(--navy)"/><circle cx="6" cy="9" r="3.5" fill="var(--navy)"/><circle cx="26" cy="9" r="3.5" fill="var(--navy)"/><path d="M7 26c0-8 4-12 9-12s9 4 9 12zM0 24c0-6 3-9 6-9l2 1c-2 2-3 5-3 8zM32 24c0-6-3-9-6-9l-2 1c2 2 3 5 3 8z" fill="var(--navy)"/></svg></div>
      <h3>Job Seekers</h3>
      <p>Sed ut perspiciatis unde omnis iste<br>natus error sit voluptatem<br>accusantium doloremque</p>
    </div>
    <div class="role" style="left:280px">
      <div class="ico"><svg width="30" height="28" viewBox="0 0 30 28"><rect x="11" y="0" width="8" height="8" fill="var(--navy)"/><rect x="0" y="20" width="8" height="8" fill="var(--navy)"/><rect x="11" y="20" width="8" height="8" fill="var(--navy)"/><rect x="22" y="20" width="8" height="8" fill="var(--navy)"/><path d="M15 8v12M4 20v-6h22v6" fill="none" stroke="var(--navy)" stroke-width="2"/></svg></div>
      <h3>Employers</h3>
      <p>Sed ut perspiciatis unde omnis iste<br>natus error sit voluptatem<br>accusantium doloremque</p>
    </div>
    <div class="role" style="left:515px">
      <div class="ico"><svg width="30" height="30" viewBox="0 0 30 30"><circle cx="12" cy="12" r="9" fill="none" stroke="var(--navy)" stroke-width="3"/><circle cx="12" cy="12" r="4" fill="var(--navy)"/><path d="M19 19l9 9" stroke="var(--navy)" stroke-width="4"/></svg></div>
      <h3>Recruiters</h3>
      <p>Sed ut perspiciatis unde omnis iste<br>natus error sit voluptatem<br>accusantium doloremque</p>
    </div>
  </div>
</section>

<section class="news">
  <h2 class="section-title">RECRUITER IN THE NEWS</h2>
  <div class="post" style="left:119px">
    <div class="photo" role="img" aria-label="Business people shaking hands in an office" style="background:linear-gradient(135deg,#dfe3e8,#7f8896 45%,#3e4656 75%,#cfd4da)"></div>
    <div class="play" style="left:197px;top:98px"></div>
    <h3>Sed ut perspiciatis unde omnis iste natus</h3>
    <div class="meta"><svg width="12" height="12" viewBox="0 0 12 12"><rect x="0" y="2" width="12" height="10" fill="var(--navy)"/><rect x="2" y="0" width="2" height="3" fill="var(--navy)"/><rect x="8" y="0" width="2" height="3" fill="var(--navy)"/><rect x="1" y="5" width="10" height="6" fill="#fff"/></svg>September 29, 2017 by Dana Whitcombe</div>
    <p>Nemo enim ipsam voluptatem quia voluptas sit aspernatur aut odit aut fugit, sed quia consequuntur magni dolores eos qui ratione voluptatem sequi nesciunt. Neque porro quisquam est, qui dolorem ipsum quia dolor sit amet, consectetur</p>
  </div>
  <div class="post" style="left:623px">
    <div class="photo" role="img" aria-label="Team gathered around a laptop in a bright office" style="background:linear-gradient(135deg,#e6ecf1,#8fa3b8 45%,#44556c 75%,#dfe5eb)"></div>
    <div class="play" style="left:197px;top:98px"></div>
    <h3>Sed ut perspiciatis unde omnis iste natus</h3>
    <div class="meta"><svg width="12" height="12" viewBox="0 0 12 12"><rect x="0" y="2" width="12" height="10" fill="var(--navy)"/><rect x="2" y="0" width="2" height="3" fill="var(--navy)"/><rect x="8" y="0" width="2" height="3" fill="var(--navy)"/><rect x="1" y="5" width="10" height="6" fill="#fff"/></svg>September 29, 2017 by Dana Whitcombe</div>
    <p>Nemo enim ipsam voluptatem quia voluptas sit aspernatur aut odit aut fugit, sed quia consequuntur magni dolores eos qui ratione voluptatem sequi nesciunt. Neque porro quisquam est, qui dolorem ipsum quia dolor sit amet, consectetur</p>
  </div>
</section>

<section class="contact">
  <div class="photo" role="img" aria-label="Soft desk scene with a plant and pen" style="inset:0;background:linear-gradient(90deg,rgba(230,226,218,.6),rgba(244,242,238,.2) 50%,rgba(200,205,190,.5))"></div>
  <h2 class="section-title">CONTACT US</h2>
  <div class="field" style="left:263px;top:138px;width:326px;height:40px">Name :</div>
  <div class="field" style="left:263px;top:189px;width:326px;height:40px">Phone :</div>
  <div class="field" style="left:263px;top:240px;width:326px;height:40px">Email :</div>
  <div class="field" style="left:609px;top:138px;width:326px;height:142px">Message :</div>
  <div class="submit">SUBMIT</div>
</section>

<footer class="footer">
  <div class="brand">HALVERN<small>STRATEGIES</small></div>
  <ul class="contact-list">
    <li><svg width="12" height="16" viewBox="0 0 12 16"><path d="M6 0a6 6 0 0 1 6 6c0 4-6 10-6 10S0 10 0 6a6 6 0 0 1 6-6z" fill="#fff"/><circle cx="6" cy="6" r="2" fill="var(--navy-deep)"/></svg><span>Halvern Strategies 4 B 12<br>00810 Northvale</span></li>
    <li><svg width="14" height="14" viewBox="0 0 14 14"><path d="M3 0l3 3-2 2c1 2 3 4 5 5l2-2 3 3-2 3C6 14 0 8 0 3z" fill="#fff"/></svg><span>Phone : (+951) 555-0142</span></li>
    <li><svg width="14" height="11" viewBox="0 0 14 11"><rect width="14" height="11" fill="#fff"/><path d="M0 0l7 6 7-6" fill="none" stroke="var(--navy-deep)" stroke-width="1.5"/></svg><span>Email: info@marcusfenwold.net</span></li>
  </ul>
  <h4 style="left:414px">QUICK LINKS</h4>
  <ul class="links">
    <li>Home</li><li>About</li><li>Recruiter</li><li>Services</li><li>Member Resources</li><li>News</li><li>Contact Us</li>
  </ul>
  <h4 style="left:645px">JOIN OUR NEWSLETTER</h4>
  <div class="newsletter">
    <p>Excepteur sint occaecat cupidatat non proident, sunt in culpa qui</p>
    <div class="input">Enter Name</div>
    <span class="subscribe">SUBSCRIBE</span>
  </div>
  <h4 style="left:1000px">SOCIAL</h4>
  <ul class="social">
    <li><span></span>Facecircle</li>
    <li><span></span>Chirper</li>
    <li><span></span>ProLink</li>
    <li><span></span>Tubecast</li>
  </ul>
  <div class="copyright">© 2017 Halvern Strategies. All Rights Reserved.</div>
</footer>

</body>
</html>
```